Lumavento business card

We need a modern business card - With our 4 colors - See web: www.lumavento.dk

I have attached logo and som old business Cards we have - Lets Make the new ones shine...:-) -

Industry/Entity Type

Business

Requirements
Must have
• the logo with lumavento only,

```html
<!DOCTYPE html>
<html lang="da">
<head>
<meta charset="utf-8">
<title>Lumavento – visitkort</title>
<link rel="stylesheet" href="https://fonts.googleapis.com/css2?family=Source+Sans+3:wght@300;400;600&display=swap">
<style>
  :root {
    --lime: #8cc657;
    --ink: #1f1f1f;
    --paper: #ffffff;
    --stage: #e9e9e9;
    --sweep: #111111;
  }
  * { margin: 0; padding: 0; box-sizing: border-box; }
  html, body {
    width: 1105px; height: 1200px; overflow: hidden;
    background: var(--stage);
    font-family: "Source Sans 3", sans-serif;
  }
  .card {
    position: absolute; left: 192px;
    width: 720px; height: 410px;
    background: var(--paper);
    overflow: hidden;
  }
  .card--front { top: 150px; }
  .card--back { top: 605px; }

  .card__sweep { position: absolute; inset: 0; }

  .holder { position: absolute; left: 36px; top: 30px; }
  .holder__name { color: var(--lime); font-size: 27px; font-weight: 600; line-height: 1.1; }
  .holder__title { color: var(--ink); font-size: 19px; font-weight: 400; margin-top: 2px; }

  .brand { position: absolute; text-align: center; }
  .brand__mark {
    display: block; margin: 0 auto 10px;
    border-radius: 50%; background: var(--lime);
  }
  .brand__name {
    color: var(--ink); font-weight: 400; letter-spacing: 0.12em;
  }
  .brand__rule { height: 3px; background: var(--lime); }
  .brand__tagline { color: var(--ink); font-weight: 400; }

  .card--front .brand { left: 137px; width: 273px; top: 96px; }
  .card--front .brand__mark { width: 62px; height: 62px; }
  .card--front .brand__name { font-size: 25px; line-height: 30px; }
  .card--front .brand__rule { margin-top: 8px; }
  .card--front .brand__tagline { font-size: 17px; margin-top: 14px; }

  .contact {
    position: absolute; right: 33px; top: 238px;
    list-style: none; text-align: right; color: var(--paper);
    font-size: 19px; line-height: 29.5px;
  }
  .contact__item { display: flex; justify-content: flex-end; align-items: center; gap: 9px; }
  .contact__icon { width: 17px; height: 17px; fill: var(--paper); flex: none; }
  .contact__address { margin-top: 2px; }

  .card--back .brand { left: 44px; width: 360px; top: 48px; }
  .card--back .brand__name { font-size: 31px; line-height: 40px; }
  .card--back .brand__rule { margin-top: 14px; }
  .card--back .brand__tagline { font-size: 20px; margin-top: 20px; }
  .card__emblem {
    position: absolute; left: 350px; top: 40px;
    width: 300px; height: 300px; border-radius: 50%;
    background: var(--lime);
  }
</style>
</head>
<body>

<section class="card card--front" aria-label="Visitkort forside">
  <svg class="card__sweep" viewBox="0 0 720 410" width="720" height="410" aria-hidden="true">
    <path fill="var(--sweep)" d="M0,346 C250,366 530,300 712,0 L720,0 L720,410 L0,410 Z"/>
    <path fill="var(--lime)" d="M0,356 C262,374 548,302 720,10 L720,410 L0,410 Z"/>
  </svg>

  <div class="holder">
    <p class="holder__name">Henrik Valsgaard</p>
    <p class="holder__title">Salgsdirektør</p>
  </div>

  <div class="brand">
    <span class="brand__mark" aria-hidden="true"></span>
    <p class="brand__name">lumavento</p>
    <div class="brand__rule"></div>
    <p class="brand__tagline">medier til unge</p>
  </div>

  <ul class="contact">
    <li class="contact__item">+45 31 20 40 60
      <svg class="contact__icon" viewBox="0 0 24 24"><path d="M6.6 10.8a15 15 0 0 0 6.6 6.6l2.2-2.2a1 1 0 0 1 1-.25 11.4 11.4 0 0 0 3.6.57 1 1 0 0 1 1 1V20a1 1 0 0 1-1 1A17 17 0 0 1 3 4a1 1 0 0 1 1-1h3.5a1 1 0 0 1 1 1c0 1.25.2 2.45.57 3.57a1 1 0 0 1-.25 1z"/></svg>
    </li>
    <li class="contact__item">+45 42 00 11 22
      <svg class="contact__icon" viewBox="0 0 24 24"><path d="M6.6 10.8a15 15 0 0 0 6.6 6.6l2.2-2.2a1 1 0 0 1 1-.25 11.4 11.4 0 0 0 3.6.57 1 1 0 0 1 1 1V20a1 1 0 0 1-1 1A17 17 0 0 1 3 4a1 1 0 0 1 1-1h3.5a1 1 0 0 1 1 1c0 1.25.2 2.45.57 3.57a1 1 0 0 1-.25 1z"/></svg>
    </li>
    <li class="contact__item">hv@lumavento.dk
      <svg class="contact__icon" viewBox="0 0 24 24"><path d="M2 5h20v14H2z M3.5 6.5 12 13l8.5-6.5" fill="var(--paper)"/><path d="M3 6l9 7 9-7" fill="none" stroke="var(--lime)" stroke-width="1.6"/></svg>
    </li>
    <li class="contact__item">www.lumavento.dk
      <svg class="contact__icon" viewBox="0 0 24 24"><circle cx="12" cy="12" r="10"/><path d="M2 12h20M12 2c3 3 3 17 0 20M12 2c-3 3-3 17 0 20" fill="none" stroke="var(--lime)" stroke-width="1.5"/></svg>
    </li>
    <li class="contact__item contact__address">Solbakkevej 14, 2000 Frederiksberg</li>
  </ul>
</section>

<section class="card card--back" aria-label="Visitkort bagside">
  <div class="brand">
    <p class="brand__name">lumavento</p>
    <div class="brand__rule"></div>
    <p class="brand__tagline">medier til unge</p>
  </div>
  <div class="card__emblem" aria-hidden="true"></div>
</section>

</body>
</html>
```